Home Remodeling company needs a business card design

we need a business card design for home remodeling company in hamilton county, indiana USA. we offers a wide range of construction services including whole house renovations, Design and Build Basements and Kitchen and Bathroom Remodeling . we would like to see designs for both site of business card that use the same color of the company logo and also including all information below :
1- Karim Feltous CEO / General Contractor
2- all company contacts Telephone numbers ( 1-888-DULOM-47 ) ( 317-555-0193) email address ( info@dulomhome.com) website ( www.dulomhome.com ) and social media logos (Facebook- twitter- google plus )
3- company logo
4- licensed . insured . bonded

```html
<!DOCTYPE html>
<html lang="en">
<head>
<meta charset="utf-8">
<title>DULOM Home Remodeling – Business Card</title>
<link href="https://fonts.googleapis.com/css2?family=Open+Sans:wght@300;400;600;800&display=swap" rel="stylesheet">
<style>
  :root {
    --bg: #e9e7e3;
    --card: #ffffff;
    --ink: #3d3d3d;
    --ink-soft: #6b6b6b;
    --band-dark: #454545;
    --band-mid: #5b5b5b;
    --red: #c9343c;
    --red-soft: #e06a70;
    --rule: #cfcfcf;
  }
  * { box-sizing: border-box; margin: 0; padding: 0; }
  html, body { width: 1200px; height: 950px; overflow: hidden; }
  body {
    background: var(--bg);
    font-family: "Open Sans", Arial, sans-serif;
    color: var(--ink);
  }
  .sheet {
    width: 1200px; height: 950px;
    display: flex; flex-direction: column;
    align-items: center; justify-content: center; gap: 30px;
  }
  .card {
    position: relative;
    width: 760px; height: 434px;
    background: var(--card);
    box-shadow: 0 6px 18px rgba(0,0,0,.18);
    overflow: hidden;
  }
  /* front */
  .brand { position: absolute; left: 48px; top: 58px; }
  .brand-name {
    display: flex; align-items: center; gap: 14px;
    font-weight: 800; font-size: 88px; line-height: 1;
    letter-spacing: -1px; color: var(--ink);
  }
  .brand-square { width: 18px; height: 18px; background: var(--red); }
  .brand-tag {
    margin-top: 8px; font-weight: 400; font-size: 19px;
    letter-spacing: 8.5px; color: var(--ink-soft);
  }
  .band { position: absolute; left: 0; top: 215px; }
  .holder { position: absolute; left: 70px; top: 222px; color: #fff; }
  .holder-name { font-weight: 600; font-size: 26px; line-height: 36px; }
  .holder-role { margin-top: 12px; font-weight: 400; font-size: 17px; color: #eeeeee; }
  .contacts {
    position: absolute; left: 150px; top: 330px;
    display: flex; align-items: stretch; gap: 30px;
    font-size: 17px; color: var(--ink);
  }
  .contact-col { display: flex; flex-direction: column; gap: 10px; }
  .contact-divider { width: 1px; background: var(--rule); }
  .contact-line { display: flex; align-items: center; gap: 10px; }
  .contact-line svg { width: 15px; height: 15px; flex: none; }
  /* back */
  .back-brand {
    position: absolute; left: 0; right: 0; top: 150px;
    display: flex; justify-content: center; align-items: center; gap: 16px;
    font-weight: 800; font-size: 92px; line-height: 1; color: var(--red);
  }
  .back-brand .brand-square { width: 20px; height: 20px; }
  .credentials {
    position: absolute; left: 0; right: 0; bottom: 44px;
    text-align: center; font-size: 18px; letter-spacing: 2px;
    color: var(--red); font-weight: 400;
  }
  .social {
    position: absolute; left: 0; right: 0; bottom: 88px;
    display: flex; justify-content: center; align-items: center; gap: 8px;
  }
  .social-rule { width: 70px; height: 1px; background: var(--rule); }
  .social-dot { width: 20px; height: 20px; border-radius: 50%; background: #555; }
</style>
</head>
<body>
<main class="sheet">

  <section class="card card-front" aria-label="Business card front">
    <div class="brand">
      <div class="brand-name">DULOM<span class="brand-square"></span></div>
      <div class="brand-tag">HOME REMODELING</div>
    </div>

    <svg class="band" width="760" height="92" viewBox="0 0 760 92" aria-hidden="true">
      <polygon points="0,0 760,0 718,46 760,92 0,92" fill="var(--band-dark)"/>
      <polygon points="0,50 726,50 718,46 760,92 0,92" fill="var(--band-mid)"/>
      <rect x="0" y="50" width="42" height="42" fill="var(--red)"/>
      <rect x="0" y="86" width="42" height="6" fill="var(--red-soft)"/>
      <rect x="736" y="40" width="12" height="12" fill="var(--red)"/>
    </svg>

    <div class="holder">
      <div class="holder-name">Karim Feltous</div>
      <div class="holder-role">CEO / General Contractor</div>
    </div>

    <div class="contacts">
      <div class="contact-col">
        <div class="contact-line">
          <svg viewBox="0 0 16 16" aria-hidden="true"><path d="M3 1.5l2.6.2 1.2 3-1.6 1.2a8 8 0 0 0 4 4l1.2-1.6 3 1.2.2 2.6c-.2 1-1 1.6-2 1.6A11.5 11.5 0 0 1 1.4 3.5c0-1 .6-1.8 1.6-2z" fill="var(--ink)"/></svg>
          <span>1-888-DULOM-47</span>
        </div>
        <div class="contact-line">
          <svg viewBox="0 0 16 16" aria-hidden="true"><rect x="4" y="1" width="8" height="14" rx="1.5" fill="none" stroke="var(--ink)" stroke-width="1.6"/><circle cx="8" cy="12.5" r="1" fill="var(--ink)"/></svg>
          <span>317-555-0193</span>
        </div>
      </div>
      <div class="contact-divider"></div>
      <div class="contact-col">
        <div class="contact-line">
          <svg viewBox="0 0 16 16" aria-hidden="true"><rect x="1" y="3" width="14" height="10" rx="1" fill="var(--ink)"/><path d="M4 8l3 3 5-6" fill="none" stroke="#fff" stroke-width="1.6"/></svg>
          <span>info@dulomhome.com</span>
        </div>
        <div class="contact-line">
          <svg viewBox="0 0 16 16" aria-hidden="true"><circle cx="8" cy="8" r="7" fill="var(--ink)"/><path d="M1 8h14M8 1c-3 3.5-3 10.5 0 14M8 1c3 3.5 3 10.5 0 14" fill="none" stroke="#fff" stroke-width="1"/></svg>
          <span>www.dulomhome.com</span>
        </div>
      </div>
    </div>
  </section>

  <section class="card card-back" aria-label="Business card back">
    <div class="back-brand">DULOM<span class="brand-square"></span></div>
    <div class="social" aria-label="Social media">
      <span class="social-rule"></span>
      <span class="social-dot"></span>
      <span class="social-dot"></span>
      <span class="social-dot"></span>
      <span class="social-rule"></span>
    </div>
    <p class="credentials">LICENSED | INSURED | BONDED</p>
  </section>

</main>
</body>
</html>
```